Postcard Design

Brivola Ftness Center is a state of the art equine rehabilitation and fitness center. We offer a wide variety of options to get your equine partner in tip top performing condition. Whether is swimming in or 11 foot deep pool or exercising in the squatted, we provide a personalized program for your special horse. Some other services offered are Tandoril breathing treatments, pelto drift and rostanel.
Updates
Project Deadline Extended Reason: Since the project was started we have opened for business and I have pictures using my equipment at our place of business that I would like to add to the project to be used. I have also received my logo design from one of your designers that I would like added to this project. Added Tuesday, March 15, 2016
Industry/Entity Type
Fitness
Look and feel
Each slider illustrates characteristics of the customer's brand and the style your logo design should communicate.

```html
<!DOCTYPE html>
<html lang="en">
<head>
<meta charset="utf-8">
<title>Brivola Ftness Center — Postcard</title>
<link rel="stylesheet" href="https://fonts.googleapis.com/css2?family=Fira+Sans:wght@400;500&family=EB+Garamond:wght@400&display=swap">
<style>
  :root {
    --ink: #111111;
    --paper: #ffffff;
    --brand-blue: #3577fa;
    --lime: #aefc48;
    --aqua: #64ffc9;
    --photo-water: #3f8f86;
    --photo-horse: #2a2128;
    --art-teal: #5fd6c4;
    --art-orange: #f2a23a;
    --art-violet: #8a4fd0;
  }
  html, body {
    margin: 0;
    padding: 0;
    width: 1200px;
    height: 1200px;
    overflow: hidden;
    background: var(--paper);
  }
  .sheet {
    position: relative;
    width: 1200px;
    height: 1200px;
    font-family: "Fira Sans", sans-serif;
    color: var(--ink);
  }
  .block { position: absolute; }

  /* Front side */
  .front-frame {
    left: 42px; top: 42px; width: 589px; height: 454px;
    border: 1px solid var(--ink); box-sizing: border-box;
  }
  .front-photo {
    left: 44px; top: 44px; width: 257px; height: 238px;
    background: linear-gradient(180deg, #6f6a5c 0%, var(--photo-horse) 35%, var(--photo-water) 60%, #1f4d4e 100%);
  }
  .front-intro {
    left: 29px; top: 282px; width: 286px; height: 214px;
    background: var(--lime);
  }
  .front-intro p {
    position: absolute; left: 20px; width: 260px; margin: 0;
    font-size: 14.2px; line-height: 19.6px; text-align: center;
  }
  .front-intro .swim { top: 35px; }
  .front-intro .extras { top: 119px; }
  .front-about {
    left: 315px; top: 312px; width: 316px; height: 183px;
    background: var(--aqua);
  }
  .front-about p {
    position: absolute; left: 0; top: 33px; width: 316px; margin: 0;
    font-size: 15.6px; line-height: 21px; text-align: center;
    color: var(--paper); letter-spacing: 0.3px;
  }
  .brand-name {
    left: 446px; top: 132px; margin: 0;
    font-size: 28px; font-weight: 500; line-height: 32px;
    color: var(--brand-blue);
  }
  .side-label {
    font-family: "EB Garamond", serif;
    font-size: 76px; line-height: 1; letter-spacing: 1px;
    margin: 0;
  }
  .label-front { left: 707px; top: 160px; }
  .label-back { left: 667px; top: 730px; }

  /* Back side */
  .back-frame {
    left: 29px; top: 619px; width: 604px; height: 468px;
    border: 1px solid var(--ink); box-sizing: border-box;
  }
  .back-bar-black { left: 28px; top: 619px; width: 159px; height: 14px; background: var(--ink); }
  .back-bar-blue { left: 187px; top: 619px; width: 133px; height: 14px; background: var(--brand-blue); }
  .back-art {
    left: 28px; top: 642px; width: 154px; height: 123px;
    background: linear-gradient(120deg, var(--art-violet) 0%, var(--art-teal) 45%, var(--art-orange) 100%);
  }
  .back-rule { left: 28px; top: 765px; width: 160px; height: 9px; background: var(--ink); }
  .back-blue-panel { left: 28px; top: 774px; width: 160px; height: 202px; background: var(--brand-blue); }
  .back-aqua-panel { left: 188px; top: 765px; width: 133px; height: 138px; background: var(--aqua); }
  .return-address { left: 326px; top: 640px; margin: 0; font-style: normal; }
  .return-address .name {
    display: block; font-size: 11.5px; font-weight: 500;
    color: var(--brand-blue); letter-spacing: 0.3px; margin-bottom: 9px;
  }
  .return-address .line {
    display: block; font-size: 10.4px; line-height: 15px; letter-spacing: 0.5px;
  }
  .address-line { left: 362px; width: 222px; height: 1.5px; background: var(--ink); }
</style>
</head>
<body>
<main class="sheet">
  <!-- Front side -->
  <div class="block front-frame"></div>
  <div class="block front-photo" role="img" aria-label="Photo of a dark horse walking through a turquoise pool with handlers on the deck"></div>
  <section class="block front-intro">
    <p class="swim">Whether is swimming in or 11 foot deep pool or exercising in the squatted, we provide a personalized program for your special horse.</p>
    <p class="extras">Some other services offered are Tandoril breathing treatments, pelto drift and rostanel.</p>
  </section>
  <section class="block front-about">
    <p>Brivola Ftness Center is a state<br>of the art equine rehabilitation and<br>fitness center. We offer a wide variety<br>of options to get your equine partner<br>in tip top performing condition.</p>
  </section>
  <h1 class="block brand-name">Brivola<br>Ftness Center</h1>
  <p class="block side-label label-front">FRONT</p>

  <!-- Back side -->
  <div class="block back-frame"></div>
  <div class="block back-bar-black"></div>
  <div class="block back-bar-blue"></div>
  <div class="block back-art" role="img" aria-label="Colourful illustrated horse head with a flowing rainbow mane"></div>
  <div class="block back-rule"></div>
  <div class="block back-blue-panel"></div>
  <div class="block back-aqua-panel"></div>
  <address class="block return-address">
    <span class="name">Brivola Ftness Center</span>
    <span class="line">123 MAIN STREET.</span>
    <span class="line">ANYWHERE, STATE ZIP</span>
  </address>
  <div class="block address-line" style="top:867px"></div>
  <div class="block address-line" style="top:903px"></div>
  <div class="block address-line" style="top:939px"></div>
  <p class="block side-label label-back">BACK</p>
</main>
</body>
</html>
```